Email Signature and a letter head

I need a professional email signature and a letter head for letters sent by post. I've attached my logo and a signature i am currently using. Current letter head is also attached.

Target Market(s)

Accounting Clients

Industry/Entity Type

Public Accounting

Font styles to use
Sans Serif

Colors

Designer to choose colors to be used in the design.

Requirements
Must have
• My logo, RM Logo, Lumo Logo, Tax Agent logo. All attached.
• All my credentials - examples in the attached documents

```html
<!DOCTYPE html>
<html lang="en">
<head>
<meta charset="utf-8">
<title>Northfield Ledger Services – Letterhead and Email Signature</title>
<link href="https://fonts.googleapis.com/css2?family=Cinzel:wght@500&family=Libre+Baskerville&family=Tinos&family=Open+Sans:wght@400;600&display=swap" rel="stylesheet">
<style>
  :root{
    --bg:#b3b3b3;
    --paper:#f8f8f8;
    --panel:#ffffff;
    --gold:#a8892c;
    --ink:#2f2f2f;
    --faint:#ececec;
    --badge-blue:#13a6d4;
    --badge-teal:#0d6f86;
    --badge-red:#c8372d;
    --badge-green:#b7c934;
    --note-blue:#2c3a8c;
    --note-green:#3b9a2d;
  }
  *{margin:0;padding:0;box-sizing:border-box}
  html,body{width:1200px;height:872px;overflow:hidden;background:var(--bg)}
  .canvas{position:relative;width:1200px;height:872px}
  .abs{position:absolute}

  .letterhead{position:absolute;left:182px;top:145px;width:411px;height:582px;background:var(--paper)}
  .email-body{position:absolute;left:626px;top:387px;width:384px;height:218px;background:var(--paper);border:1px solid #d6d6d6}

  .sender-name{font-family:"Libre Baskerville",serif;color:var(--gold);white-space:nowrap}
  .ids{font-family:"Tinos",serif;color:var(--ink);white-space:nowrap}
  .ids .label{color:var(--gold)}
  .ids .sep{color:var(--gold);margin:0 4px}
  .contacts{font-family:"Tinos",serif;color:var(--ink);list-style:none;white-space:nowrap}
  .contacts li{display:flex;align-items:center}
  .contacts svg{flex:none;margin-right:4px}
  .brand-name{font-family:"Cinzel",serif;color:var(--gold);text-align:center;white-space:nowrap}
  .brand-tag{font-family:"Cinzel",serif;color:var(--gold);text-align:center;white-space:nowrap}
  .tax-label{font-family:"Open Sans",sans-serif;font-weight:600;color:var(--ink);line-height:1.15;white-space:nowrap}
  .watermark-name{font-family:"Cinzel",serif;color:var(--faint);text-align:center;white-space:nowrap}
  .disclaimer{font-family:"Open Sans",sans-serif;color:var(--note-blue)}
  .eco-note{font-family:"Open Sans",sans-serif;color:var(--note-green);white-space:nowrap}
</style>
</head>
<body>
<div class="canvas">

  <!-- Letterhead -->
  <section class="letterhead" aria-label="Letterhead">
    <svg class="abs" style="left:0;top:0" width="411" height="582" viewBox="0 0 411 582" aria-hidden="true">
      <circle cx="207" cy="318" r="146" fill="none" stroke="var(--faint)" stroke-width="8"/>
      <path d="M20 62 H190 C205 62 212 78 222 90 C228 98 233 100 242 100 H392" fill="none" stroke="var(--gold)" stroke-width="1.2"/>
      <circle cx="334" cy="49" r="25" fill="none" stroke="var(--gold)" stroke-width="2"/>
      <line x1="214" y1="554" x2="392" y2="554" stroke="var(--gold)" stroke-width="1.2"/>
      <circle cx="32" cy="542" r="13" fill="var(--badge-blue)"/>
      <circle cx="59" cy="542" r="13" fill="var(--badge-teal)"/>
      <rect x="91" y="531" width="14" height="14" fill="none" stroke="var(--badge-red)" stroke-width="2"/>
      <circle cx="135" cy="542" r="12" fill="var(--badge-green)"/>
    </svg>
    <div class="abs watermark-name" style="left:57px;top:300px;width:300px;font-size:30px">Northfield</div>

    <div class="abs sender-name" style="left:20px;top:31px;font-size:12px">Delphine Marsh RM BBus.</div>
    <div class="abs ids" style="left:20px;top:46px;font-size:7.5px"><span class="label">ABN:</span> 41 207 553 918<span class="sep">|</span><span class="label">TAN:</span> 318 904 27</div>
    <ul class="abs contacts" style="left:20px;top:67px;font-size:7.2px;line-height:8.4px">
      <li><svg width="5" height="5" viewBox="0 0 10 10"><path d="M1 3h8v6H1z M3 1h4v2H3z" fill="var(--gold)"/></svg>0400118247</li>
      <li><svg width="5" height="5" viewBox="0 0 10 10"><circle cx="5" cy="5" r="4.5" fill="var(--gold)"/></svg>www.northfieldledgerservices.com.au</li>
      <li><svg width="5" height="5" viewBox="0 0 10 10"><rect x="0" y="2" width="10" height="6" fill="var(--gold)"/></svg>Delphine@northfieldledgerservices.com.au</li>
      <li><svg width="5" height="6" viewBox="0 0 10 12"><path d="M5 12 L1 6 A4.3 4.3 0 1 1 9 6 Z" fill="var(--gold)"/></svg>17 Harbour Lane Seaview East VIC 3100</li>
    </ul>
    <div class="abs brand-name" style="left:264px;top:76px;width:140px;font-size:11.5px">Northfield Ledger</div>
    <div class="abs brand-tag" style="left:264px;top:90px;width:140px;font-size:5px;letter-spacing:1.6px">Business Services</div>

    <div class="abs tax-label" style="left:151px;top:536px;font-size:5px">Tax Agent<br>31890427</div>
  </section>

  <!-- Email signature -->
  <section class="email-body" aria-label="Email signature">
    <svg class="abs" style="left:0;top:0" width="384" height="218" viewBox="0 0 384 218" aria-hidden="true">
      <path d="M9 79 H178 C192 79 198 94 206 105 C212 114 217 118 226 118 H374" fill="none" stroke="var(--gold)" stroke-width="1.2"/>
      <circle cx="218" cy="51" r="9" fill="var(--badge-blue)"/>
      <circle cx="237" cy="51" r="9" fill="var(--badge-teal)"/>
      <rect x="225" y="68" width="10" height="10" fill="none" stroke="var(--badge-red)" stroke-width="1.6"/>
      <circle cx="218" cy="97" r="8" fill="var(--badge-green)"/>
      <circle cx="318" cy="66" r="24" fill="none" stroke="var(--gold)" stroke-width="1.8"/>
      <path d="M19 169 h12 v-6 l-4 -4 h-4 z M24 159 l2 -5 l2 5" fill="var(--note-green)"/>
    </svg>

    <div class="abs sender-name" style="left:9px;top:51px;font-size:12px">Delphine Marsh RM BBus.</div>
    <div class="abs ids" style="left:9px;top:66px;font-size:7.2px"><span class="label">ABN:</span> 41 207 553 918<span class="sep">|</span><span class="label">TAN:</span> 318 904 27</div>
    <ul class="abs contacts" style="left:9px;top:86px;font-size:7px;line-height:8.2px">
      <li><svg width="5" height="5" viewBox="0 0 10 10"><path d="M1 3h8v6H1z M3 1h4v2H3z" fill="var(--gold)"/></svg>0400118247</li>
      <li><svg width="5" height="5" viewBox="0 0 10 10"><circle cx="5" cy="5" r="4.5" fill="var(--gold)"/></svg>www.northfieldledgerservices.com.au</li>
      <li><svg width="5" height="5" viewBox="0 0 10 10"><rect x="0" y="2" width="10" height="6" fill="var(--gold)"/></svg>Delphine@northfieldledgerservices.com.au</li>
      <li><svg width="5" height="6" viewBox="0 0 10 12"><path d="M5 12 L1 6 A4.3 4.3 0 1 1 9 6 Z" fill="var(--gold)"/></svg>17 Harbour Lane Seaview East VIC 3100</li>
    </ul>
    <div class="abs tax-label" style="left:228px;top:92px;font-size:4.2px">Tax Agent<br>31890427</div>
    <div class="abs brand-name" style="left:254px;top:94px;width:130px;font-size:11px">Northfield Ledger</div>
    <div class="abs brand-tag" style="left:254px;top:107px;width:130px;font-size:5px;letter-spacing:1.5px">Business Services</div>

    <p class="abs disclaimer" style="left:9px;top:130px;width:340px;font-size:4.6px;line-height:6.5px">This e-mail and its attachments are confidential and privileged. Any unauthorised use is expressly prohibited. If you receive this e-mail in error please contact us, then delete the e-mail.</p>
    <p class="abs eco-note" style="left:46px;top:160px;font-size:5px">Please consider the environment before printing this e-mail notice.</p>
  </section>

</div>
</body>
</html>
```